Varentoria Business Card and Letter Head

We are a leadership assessment consultancy based in Sydney, Australia. We help executive-level decison-makers select leaders for more senior level roles in corporate and government organisations. Our methodology is based on the latest research from the field of neuroscience.
We need a business card design and matching letter head that presents our company, Varentoria, as a:
1. trusted adviser to senior executive-level decison makers
2. niche consultancy who are experts in the field of assessing leadership talent
3. results-focused solution provider who balance scientific methods with pragmatic solutions
The following company details should be used in all designs:
Company Name: Varentoria
Details (for business card):
Derek Hanford
Prime Capacity Officer
Level 29, Marlow Tower
7 Marlow Square
Sydney, NSW 2000 Australia
Phone: 1300 582 714
Mobile: 0412 637 258
Email: derek.hanford@varentoria-example.com.au
Website: varentoria-example.com.au
I have attached the logo for Varentoria (for both a white and black background) - your business card and letter head designs must incoporate this logo and colour scheme.
Thanks for your interest in this project, I'm looking forward to receiving your ideas.
Regards,
Derek
Target Market(s)
Executive-level decison-makers in corporate and government organisations (e.g., CEO, VP, Head of Human Resources)
Industry/Entity Type
Leadership
Look and feel

```html
<!DOCTYPE html>
<html lang="en">
<head>
<meta charset="utf-8">
<title>Varentoria Business Card</title>
<link href="https://fonts.googleapis.com/css2?family=Source+Sans+3:wght@400;600;700&display=swap" rel="stylesheet">
<style>
  :root {
    --backdrop: #e6e2dc;
    --card: #ffffff;
    --charcoal: #3d3d3f;
    --accent-red: #c0301f;
    --text-grey: #555557;
    --on-dark: #ffffff;
  }
  * { margin: 0; padding: 0; box-sizing: border-box; }
  html, body { width: 1200px; height: 469px; overflow: hidden; }
  body {
    background: var(--backdrop);
    font-family: "Source Sans 3", Arial, sans-serif;
    position: relative;
  }
  .card {
    position: absolute;
    top: 81px;
    width: 526px;
    height: 302px;
    background: var(--card);
    box-shadow: 0 2px 6px rgba(0,0,0,0.18);
  }
  .card--front { left: 57px; }
  .card--back { left: 609px; }
  .brand {
    position: absolute;
    top: 58px;
    left: 105px;
    display: flex;
    align-items: center;
    gap: 16px;
  }
  .brand__square {
    width: 52px;
    height: 52px;
    background: var(--charcoal);
  }
  .brand__name {
    font-size: 56px;
    font-weight: 700;
    color: var(--charcoal);
    letter-spacing: -1px;
    line-height: 1;
  }
  .band-accent {
    position: absolute;
    left: 0;
    top: 171px;
    width: 34px;
    height: 32px;
    background: var(--accent-red);
  }
  .band {
    position: absolute;
    left: 40px;
    right: 0;
    top: 171px;
    height: 32px;
    background: var(--charcoal);
    color: var(--on-dark);
    display: flex;
    align-items: center;
    justify-content: center;
  }
  .band__name { font-size: 16px; font-weight: 700; margin-right: 8px; }
  .band__role { font-size: 12.5px; }
  .band__web { font-size: 14px; }
  .address {
    position: absolute;
    top: 218px;
    right: 276px;
    text-align: right;
    font-size: 11.5px;
    line-height: 16.5px;
    color: var(--text-grey);
  }
  .divider {
    position: absolute;
    left: 263px;
    top: 217px;
    width: 1px;
    height: 46px;
    background: var(--text-grey);
  }
  .contacts {
    position: absolute;
    top: 218px;
    left: 273px;
    list-style: none;
    font-size: 11.5px;
    line-height: 16.5px;
    color: var(--text-grey);
  }
  .contacts li { display: flex; align-items: center; gap: 7px; }
  .contacts svg { width: 10px; height: 10px; fill: var(--text-grey); }
  .website {
    position: absolute;
    top: 273px;
    left: 190px;
    font-size: 11.5px;
    color: var(--text-grey);
  }
</style>
</head>
<body>
  <section class="card card--front">
    <div class="brand">
      <span class="brand__square"></span>
      <span class="brand__name">Varentoria</span>
    </div>
    <div class="band-accent"></div>
    <div class="band">
      <span class="band__name">Derek Hanford,</span>
      <span class="band__role">Prime Capacity Officer</span>
    </div>
    <p class="address">Level 29, Marlow Tower<br>7 Marlow Square<br>Sydney, NSW 2000 Australia</p>
    <div class="divider"></div>
    <ul class="contacts">
      <li><svg viewBox="0 0 10 10"><path d="M2 0.5 L4 2.6 L3 3.8 Q4 6 6.2 7 L7.4 6 L9.5 8 L8 9.5 Q2 9 0.5 2 Z"/></svg>1300 582 714</li>
      <li><svg viewBox="0 0 10 10"><path d="M2.5 0 H7.5 V10 H2.5 Z M3.3 1 V7 H6.7 V1 Z"/></svg>0412 637 258</li>
      <li><svg viewBox="0 0 10 10"><path d="M0 2 H10 V8 H0 Z M0.8 2.6 L5 5.6 L9.2 2.6 Z" fill-rule="evenodd"/></svg>derek.hanford@varentoria-example.com.au</li>
    </ul>
    <p class="website">www.varentoria-example.com.au</p>
  </section>

  <section class="card card--back">
    <div class="brand">
      <span class="brand__square"></span>
      <span class="brand__name">Varentoria</span>
    </div>
    <div class="band-accent"></div>
    <div class="band">
      <span class="band__web">www.varentoria-example.com.au</span>
    </div>
  </section>
</body>
</html>
```